website update

We need to redesign our current website to be more personalised and sophisticated. We are physiotherapy clinic based in sydney australia, offer a range of clinical service such as Physiotherapy, Massage, sports injuries rehabilitation, Women's health (incontinency etc), Pilates classes, back pain exercise program, acupuncture, Gait analysis.
our current website is www.brightlanehealth.com.au
an example of ideal website is http://quillbrookrehabstudio.com/
homepage: with a revolving displaying attached photos which is linked to relevants page

```html
<!DOCTYPE html>
<html lang="en">
<head>
<meta charset="utf-8">
<title>Brightlane Physiotherapy &amp; Sports Clinic</title>
<link href="https://fonts.googleapis.com/css2?family=Open+Sans:wght@400;600;700&family=Roboto:wght@400;500;700&display=swap" rel="stylesheet">
<style>
:root{
  --green:#8ab828;
  --green-dark:#2f8f4a;
  --btn-green:#3f9b5a;
  --ink:#444;
  --muted:#666;
  --grey-band:#e6e6e6;
  --top-bar:#ececec;
  --tile:#555;
  --field:#e8e8e8;
  --blue:#1b6a9c;
}
*{margin:0;padding:0;box-sizing:border-box}
html,body{width:1200px;height:2459px;overflow:hidden;background:#fff}
body{position:relative;font-family:"Open Sans",Arial,sans-serif;color:var(--ink)}
.abs{position:absolute}

.top-bar{left:0;top:0;width:1200px;height:52px;background:var(--top-bar)}
.social{left:98px;top:19px;display:flex;gap:10px}
.social span{width:13px;height:13px;border-radius:50%;background:#7a8a9a}
.appointment{left:880px;top:10px;width:220px;height:31px;background:var(--btn-green);color:#fff;font:600 14px "Roboto",sans-serif;display:flex;align-items:center;justify-content:center;border-radius:2px}

.brand{left:102px;top:70px;display:flex;align-items:center;gap:14px}
.brand-mark{width:66px;height:66px;border-radius:50%;background:var(--green)}
.brand-name{font:700 38px "Open Sans",sans-serif;color:var(--green);line-height:1}
.brand-sub{font:600 12px "Open Sans",sans-serif;color:var(--green);letter-spacing:.5px;margin-top:4px}
.address{top:72px;font:400 13px "Roboto",sans-serif;color:#555;width:220px}
.address h4{font-weight:400;font-size:13.5px;margin-bottom:6px}
.address p{font-size:11px;line-height:14px;padding-left:22px;position:relative}
.address p i{position:absolute;left:2px;top:4px;width:8px;height:6px;background:#777}

.nav{left:0;top:156px;width:1200px;height:47px;background:var(--green);display:flex;align-items:center;padding-left:102px}
.nav a{font:500 14px "Roboto",sans-serif;color:#fff;text-decoration:none;height:47px;display:flex;align-items:center;padding:0 22px}
.nav a.active{background:var(--green-dark);padding:0 20px}

.slider{left:102px;top:231px;width:998px;height:474px;background:linear-gradient(120deg,#1e2b4a 0%,#3a4f78 35%,#d9d6d0 55%,#b8405a 75%,#222 100%)}
.slide-arrow{top:436px;width:32px;height:32px;border-radius:50%;background:rgba(255,255,255,.75);display:flex;align-items:center;justify-content:center}
.caption-a{left:188px;top:539px;width:217px;height:41px;background:var(--green);color:#fff;font:400 24px "Open Sans",sans-serif;display:flex;align-items:center;justify-content:center}
.caption-b{left:188px;top:583px;width:342px;height:43px;background:#3a3a3a;color:#fff;font:400 24px "Open Sans",sans-serif;display:flex;align-items:center;justify-content:center}
.slider-shadow{left:150px;top:705px;width:900px;height:50px;background:radial-gradient(ellipse at top,rgba(0,0,0,.18),rgba(0,0,0,0) 70%)}

.intro{top:776px;width:298px}
.intro h2{font:600 24px "Open Sans",sans-serif;color:#444;padding-bottom:8px;border-bottom:2px solid #bbb}
.intro .thumb{float:left;width:146px;height:148px;margin:16px 20px 6px 0}
.intro p{font:400 12.5px/17px "Open Sans",sans-serif;color:#555;text-align:justify;padding-top:16px}
.intro p.rest{padding-top:0;clear:both}
.read-more{top:1147px;width:98px;height:21px;color:#fff;font:600 12px "Open Sans",sans-serif;display:flex;align-items:center;justify-content:center}

.services{left:0;top:1224px;width:1200px;height:484px;background:var(--grey-band)}
.section-title{width:1200px;left:0;text-align:center;font:600 24px "Open Sans",sans-serif;color:#444}
.service{width:260px;text-align:center}
.service .tile{width:110px;height:110px;margin:0 auto;background:var(--tile);display:flex;align-items:center;justify-content:center}
.service .tile.on{background:var(--green);box-shadow:3px 3px 0 rgba(0,0,0,.15)}
.service span{display:block;margin-top:14px;font:600 16px "Open Sans",sans-serif;color:#444}

.partner{top:1814px;width:182px;height:105px;border:1px solid #d5d5d5;display:flex;align-items:center;justify-content:center}
.partner i{display:block;width:140px;height:60px}

.divider{left:0;top:1991px;width:1200px;height:2px;background:#e2e2e2}
.badge{top:2065px;height:48px}
.footer-info{left:102px;top:2136px;width:300px;font:400 13px/18px "Open Sans",sans-serif;color:#666}
.footer-info p{margin-bottom:12px}
.location{left:102px;top:2271px;font:700 12px "Roboto",sans-serif;color:#e08a00;border-bottom:1px solid #ccc;padding-bottom:2px}
.foot-social{left:102px;top:2306px;display:flex;gap:6px}
.foot-social span{width:24px;height:24px;background:#2d5f96}

.contact-title{left:449px;top:2062px;font:700 22px "Roboto",sans-serif;color:var(--blue)}
.field{background:var(--field);font:400 13px "Open Sans",sans-serif;color:#555;padding:0 14px;display:flex;align-items:center}
.field.area{align-items:flex-start;padding-top:14px}
.send{left:452px;top:2304px;width:68px;height:36px;border:2px solid var(--blue);color:var(--blue);font:700 14px "Roboto",sans-serif;display:flex;align-items:center;justify-content:center;background:#fff}

.bottom-bar{left:0;top:2403px;width:1200px;height:56px;background:var(--green);color:#fff;font:400 12.5px "Open Sans",sans-serif;display:flex;align-items:center;justify-content:space-between;padding:0 30px 0 102px}
.bottom-bar .links{display:flex;gap:80px}
</style>
</head>
<body>

<div class="abs top-bar"></div>
<div class="abs social"><span></span><span></span><span></span><span></span><span></span></div>
<div class="abs appointment">Schedule Online Appointment</div>

<div class="abs brand">
  <div class="brand-mark"></div>
  <div>
    <div class="brand-name">brightlane</div>
    <div class="brand-sub">PHYSIOTHERAPY &amp; SPORTS CLINIC</div>
  </div>
</div>
<div class="abs address" style="left:620px">
  <h4>Address Line 1</h4>
  <p><i></i>info@brightlanehealth.com.au</p>
  <p><i></i>Arcade, 212 Wattle St,<br>Elmsford 2069</p>
</div>
<div class="abs address" style="left:890px">
  <h4>Address Line 2</h4>
  <p><i></i>info@brightlanehealth.com.au</p>
  <p><i></i>Shop2, 18-24 Banksia Rd, Corrowa 2114<br>Australia</p>
</div>

<nav class="abs nav">
  <a class="active">Home</a><a>About us</a><a>Common conditions</a><a>Treatments</a><a>Specialised services</a><a>OH&amp;S / Workplace Assessment</a><a>Contact Us</a>
</nav>

<div class="abs slider" role="img" aria-label="Physiotherapist performing an ultrasound assessment on a patient lying on a treatment bed"></div>
<div class="abs slide-arrow" style="left:128px"><svg width="12" height="14" viewBox="0 0 12 14"><path d="M9 1 3 7l6 6" stroke="#444" stroke-width="2.5" fill="none"/></svg></div>
<div class="abs slide-arrow" style="left:1040px"><svg width="12" height="14" viewBox="0 0 12 14"><path d="M3 1l6 6-6 6" stroke="#444" stroke-width="2.5" fill="none"/></svg></div>
<div class="abs caption-a">Brightlane</div>
<div class="abs caption-b">Enjoy The Freedom Again</div>
<div class="abs slider-shadow"></div>

<section class="abs intro" style="left:102px">
  <h2>About Us</h2>
  <div class="thumb" role="img" aria-label="Colour pressure map of foot scans" style="background:linear-gradient(135deg,#0a1a40,#2d8c3c 40%,#e8c42a 60%,#c8261e 80%,#0a1a40)"></div>
  <p>At Brightlane Physiotherapy Clinic we believe that effective treatments come with accurate diagnosis. In the clinic we have the latest clinically-proven equipments</p>
  <p class="rest">which will improve the accuracy in the diagnosis of your conditions and pain. We offer in-house assessment services include the use of real-time ultrasound device(to assess muscle weakness &amp; soft-tissue injuries), computerised posture/spinal assessment, computer analysis for walking and running, and computerised foot assessment. Special</p>
</section>
<section class="abs intro" style="left:452px">
  <h2>Who are we?</h2>
  <div class="thumb" role="img" aria-label="Physiotherapist treating a patient in the clinic" style="background:linear-gradient(135deg,#e9e4de,#c9b7a8 50%,#8a6e5e)"></div>
  <p>At BRIGHTLANE we are dedicated to providing the highest quality, conservative treatment options. In the management of sports injuries and back pain we provide strategies include</p>
  <p class="rest">Injury prevention and biomechanical corrections to optimise performance drestore paind restore pain-free participation in daily activies and sports, without unnecessary or prolonged care</p>
</section>
<section class="abs intro" style="left:801px">
  <h2>How we do it?</h2>
  <div class="thumb" role="img" aria-label="Acupuncture needles placed in a hand" style="background:linear-gradient(135deg,#2a2a2a,#c9906e 50%,#3a3a3a)"></div>
  <p>Our physiotherapists integrate the latest and most proven exercise &amp; sports science and hands-on therapies to treat musculoskeletal injuries.</p>
  <p class="rest">Our treatments are always tailored to a broad range of patients, including those recovering from acute sports injury, those managing complex chronic conditions and those seeking improved physical performance.</p>
</section>
<div class="abs read-more" style="left:302px;background:var(--btn-green)">Read More</div>
<div class="abs read-more" style="left:652px;background:#555">Read More</div>
<div class="abs read-more" style="left:1002px;background:#555">Read More</div>

<div class="abs services"></div>
<h2 class="abs section-title" style="top:1252px">Our Service's</h2>

<div class="abs service" style="left:73px;top:1344px"><div class="tile on"><svg width="50" height="50" viewBox="0 0 50 50" fill="#fff"><circle cx="32" cy="9" r="5"/><path d="M20 18l12-3 6 10 7 1-1 4-9-1-4-5-3 9 6 6-3 10-4-1 2-8-7-5-5 8-9 1 0-4 6-1 6-12 1-6-5 2-3 7-4-2 4-9z"/></svg></div><span>Physiotherapy</span></div>
<div class="abs service" style="left:334px;top:1344px"><div class="tile"><svg width="52" height="40" viewBox="0 0 52 40" fill="#fff"><circle cx="12" cy="24" r="5"/><rect x="16" y="24" width="30" height="7" rx="3"/><circle cx="28" cy="6" r="5"/><path d="M24 12h8l4 10h-4l-3-6-4 6h-4z"/><rect x="4" y="33" width="44" height="3"/></svg></div><span>Massage</span></div>
<div class="abs service" style="left:594px;top:1344px"><div class="tile"><svg width="44" height="50" viewBox="0 0 44 50" fill="none" stroke="#fff" stroke-width="3"><circle cx="22" cy="9" r="6"/><path d="M8 48V26q0-8 8-8h12q8 0 8 8v22"/><path d="M14 30l8 6 8-6" /></svg></div><span>Sports injuries rehabilitation</span></div>
<div class="abs service" style="left:855px;top:1344px"><div class="tile"><svg width="44" height="50" viewBox="0 0 44 50" fill="#fff"><circle cx="22" cy="14" r="10"/><path d="M4 48q0-20 18-20t18 20z"/></svg></div><span>Women's health</span></div>

<div class="abs service" style="left:73px;top:1524px"><div class="tile"><svg width="52" height="44" viewBox="0 0 52 44" fill="#fff"><circle cx="16" cy="8" r="5"/><path d="M10 16l20 10 14-6 2 4-16 8-22-10z"/><rect x="4" y="38" width="44" height="3"/></svg></div><span>Pilates classes</span></div>
<div class="abs service" style="left:334px;top:1524px"><div class="tile"><svg width="40" height="54" viewBox="0 0 40 54" fill="#fff"><circle cx="18" cy="7" r="5"/><path d="M13 14h10q6 4 4 14l-4 4v20h-5V34l-5-4z"/><circle cx="30" cy="22" r="2" fill="#e33"/></svg></div><span>Back pain exercise program</span></div>
<div class="abs service" style="left:594px;top:1524px"><div class="tile"><svg width="52" height="44" viewBox="0 0 52 44" fill="#fff"><path d="M4 10q10-6 22-2l20-2v6H28q-4 8-14 8z"/><rect x="30" y="16" width="2" height="24"/><circle cx="31" cy="16" r="3"/></svg></div><span>Acupuncture</span></div>
<div class="abs service" style="left:855px;top:1524px"><div class="tile"><svg width="44" height="44" viewBox="0 0 44 44" fill="#fff"><path d="M22 4l12 13h-8v12h-8V17h-8z"/><path d="M4 26h5v10h26V26h5v15H4z"/></svg></div><span>Gait analysis</span></div>

<h2 class="abs section-title" style="top:1743px">Our Partners</h2>
<div class="abs partner" style="left:102px"><i style="background:#1a9ad6"></i></div>
<div class="abs partner" style="left:305px"><i style="background:#0a8a4e"></i></div>
<div class="abs partner" style="left:510px"><i style="background:#d2213b;border-radius:30px"></i></div>
<div class="abs partner" style="left:715px"><i style="background:#d8103c"></i></div>
<div class="abs partner" style="left:918px"><i style="background:#2a8a3a;border-radius:8px"></i></div>

<div class="abs divider"></div>

<div class="abs badge" style="left:102px;width:98px;background:#c8d4ea;border-radius:4px"></div>
<div class="abs badge" style="left:222px;width:120px;background:#d6e6f2;border-radius:24px"></div>
<div class="abs footer-info">
  <p>Email: info@brightlanehealth.com.au</p>
  <p>Shop 8, The Arcade, 212 Wattle St,<br>Elmsford 2069 &nbsp;[See a map]</p>
  <p>Undefined Shop2, 18-24 Banksia Rd, Corrowa 2114<br>Australia &nbsp;[See a map]</p>
</div>
<div class="abs location">Location</div>
<div class="abs foot-social"><span></span><span style="background:#2a9fd6"></span><span style="background:#1e6ea8"></span><span style="background:#c9402c"></span></div>

<h3 class="abs contact-title">Contact Us</h3>
<div class="abs field" style="left:449px;top:2109px;width:320px;height:37px">Name</div>
<div class="abs field" style="left:778px;top:2109px;width:320px;height:37px">Email</div>
<div class="abs field area" style="left:449px;top:2157px;width:649px;height:136px">Type Your Message</div>
<div class="abs send">Send</div>

<footer class="abs bottom-bar">
  <span>© 2014 yoursite. all rights reserved</span>
  <div class="links"><span>Northwind Studio. Terms | Privacy | Contact Us</span><span>M3</span></div>
</footer>

</body>
</html>
```